Project Overview:
We are looking to create a website for a monthly subscription IPTV service in WordPress. The website should provide a seamless user experience for customers to sign up for the service and manage their account information. We need the following pages: Home Page, Product Page, Sign-Up Page, and Account Information Page.

Home Page:
The Home Page design should be simple and clean, with a dark theme and minimalistic design elements. We would like to include graphics of popular movie shows displayed on multiple devices. The page should highlight the key benefits and features of our service and provide a clear call-to-action for visitors to sign up.

Product Page:
The Product Page should provide detailed information about our subscription tiers and pricing plans. It should highlight the key features of each plan and provide a clear comparison between them. The page should also include a call-to-action button for visitors to sign up.

Sign-Up Page:
The Sign-Up Page is the conversion page where members will sign up for the service. It should collect the following information: Name, Phone Number, Email, Password, and Payment Information. The design should be simple, intuitive, and easy to use. It should highlight the benefits of our service and provide a clear call-to-action for visitors to sign up.

Account Information Page:
The Account Information Page should allow members to view and manage their account details. It should include the following information: Profile Image, Contact Details, Password Management, Payment Information Management, and Membership Expiration Date. The design should be user-friendly, intuitive, and easy to navigate.

Goals: The primary goal of the website is to provide an easy-to-use portal for customers to sign up for the service and manage their account information. The website should be user-friendly and visually appealing to attract potential customers.

Scope: The scope of the project includes designing a home page, a sign-up page, an account information page, and a payment information page. The website should be designed to be responsive and accessible on desktop and mobile devices.

Design Preferences: The design should be clean, modern, and visually appealing. The use of a color palette that is consistent with the brand identity is recommended. The website should be easy to navigate and provide a clear call-to-action for users to sign up for the service.

FYI: The subscription service I am designing a website for is related to an IPTV service. IPTV stands for Internet Protocol Television, which is a digital television broadcasting protocol that uses the internet to deliver TV programs and videos to viewers. The website will allow customers to sign up for the IPTV service and access their account information such as user name and password, membership tier, name, and payment details. Please let me know if you have any further questions, and I would be happy to provide more details. Thank you!

Dear Designers,

Thank you for your participation in our project. After reviewing the designs received so far, we have decided to update the brief to better reflect our needs and preferences. We apologize for any confusion this may cause, but we believe that these changes will result in better design submissions and a more successful project overall.

The updated brief is as follows:

We are looking to create a website for WordPress.

Also, here is the updated Brief.

Project Title: WordPress Website Design for Monthly Subscription IPTV Service

Project Overview:
We are looking to create a website for a monthly subscription IPTV service. The website should provide a seamless user experience for customers to sign up for the service and manage their account information. We need the following pages: Home Page, Product Page, Sign-Up Page, and Account Information Page.

Home Page:

Product Page:

Sign-Up Page:

Account Information Page:

Design Preferences:
We prefer a dark theme with minimalistic design elements and hits of our logo colors. The website should be easy to use and navigate, with clear calls-to-action and simple, intuitive forms. The design should be optimized for mobile devices and load quickly.

We hope that these updates provide you with a clearer understanding of our requirements and preferences. Please let us know if you have any questions or concerns. We look forward to seeing your revised designs.

Thank you again for your participation.
We will guarantee this project as soon as we see something we like that meets the updated requirements.

The website's target audience is individuals who are interested in subscribing to the monthly service.

4 page

• One item for sale and a client profile section.

```html
<!DOCTYPE html>
<html lang="en">
<head>
<meta charset="utf-8">
<title>VORTIQ – IPTV Subscription</title>
<link href="https://fonts.googleapis.com/css2?family=Permanent+Marker&family=Lato:wght@400;700&family=Poppins:wght@500;600&display=swap" rel="stylesheet">
<style>
  :root{
    --bg:#0b0b0d;
    --bg-2:#121216;
    --bg-3:#16161c;
    --red:#ff0f0f;
    --red-dark:#c80a0a;
    --white:#ffffff;
    --text:#e6e6e6;
    --muted:#bdbdbd;
  }
  *{margin:0;padding:0;box-sizing:border-box}
  html,body{width:1200px;height:3304px;overflow:hidden;background:var(--bg)}
  body{position:relative;font-family:"Lato",Arial,sans-serif;color:var(--text)}
  .section{position:absolute;left:0;width:1200px;overflow:hidden}
  .abs{position:absolute}
  .display{font-family:"Permanent Marker",Impact,"Arial Narrow",sans-serif;color:var(--white);font-weight:400;letter-spacing:-0.5px;white-space:nowrap;z-index:2}
  .display .accent{color:var(--red)}
  .btn{position:absolute;display:flex;align-items:center;justify-content:center;background:var(--red);color:var(--white);border-radius:30px;font-family:"Poppins",Arial,sans-serif;font-weight:600;text-decoration:none;white-space:nowrap;z-index:2}
  .brand{font-family:"Lato",Arial,sans-serif;font-weight:700;color:var(--white);display:flex;align-items:center;gap:12px;letter-spacing:2px}
  .brand .mark{background:var(--red);display:block}

  /* hero */
  .hero{top:0;height:682px;background:radial-gradient(ellipse at 30% 40%,#2a2a32 0%,#141418 55%,#0b0b0d 100%)}
  .hero .brand{left:97px;top:22px;font-size:50px}
  .hero .brand .mark{width:22px;height:22px}
  .nav{position:absolute;top:44px;left:609px;display:flex;gap:40px;font-size:16px}
  .nav a{color:var(--white);text-decoration:none}
  .nav a.active{color:var(--red);font-weight:700;text-decoration:underline}
  .hero .contact{left:958px;top:30px;width:146px;height:51px;font-size:18px}
  .hero h1{left:97px;top:206px;width:400px;font-size:76px;line-height:86px}
  .hero p{left:97px;top:383px;width:390px;font-size:16px;line-height:31px;color:var(--white);z-index:2}
  .hero .signup{left:97px;top:485px;width:125px;height:51px;font-size:18px}
  .devices{left:530px;top:160px;width:626px;height:350px;border-radius:10px;background:linear-gradient(135deg,#3a3f4a 0%,#1f5f6a 45%,#b07a3a 100%);opacity:.85;z-index:1}

  /* about */
  .about{top:682px;height:585px;background:radial-gradient(ellipse at 25% 55%,#1c1c2c 0%,#101014 60%,#0b0b0d 100%)}
  .phones{left:96px;top:87px;width:458px;height:417px;border-radius:30px;background:linear-gradient(160deg,#0f3a4a 0%,#1fa0c0 45%,#402018 100%)}
  .about h2{left:586px;top:96px;font-size:32px}
  .about p{left:586px;top:146px;width:525px;font-size:15.5px;line-height:30.8px;color:var(--white)}
  .about .more{left:586px;top:441px;width:128px;height:46px;font-family:"Permanent Marker",Impact,sans-serif;font-weight:400;font-size:16px}

  /* benefits */
  .benefits{top:1267px;height:585px;background:linear-gradient(180deg,#0d0d10 0%,#141418 50%,#0d0d10 100%)}
  .benefits h2{left:0;width:1200px;top:38px;text-align:center;font-size:32px}
  .benefits .lead{left:0;width:1200px;top:96px;text-align:center;font-size:15.5px;line-height:31px;color:var(--white)}
  .card{position:absolute;top:174px;width:312px;height:337px;border:2px solid var(--red);background:rgba(20,20,26,.75);text-align:center}
  .card .icon{position:absolute;left:99px;top:28px;width:110px;height:110px;border-radius:50%;background:var(--white);display:flex;align-items:center;justify-content:center}
  .card .icon.on{background:var(--red)}
  .card h3{position:absolute;top:152px;left:0;width:100%;font-size:18px}
  .card p{position:absolute;top:188px;left:14px;right:14px;font-size:15.5px;line-height:31px;color:var(--white)}
  .card a{position:absolute;top:290px;left:0;width:100%;font-family:"Permanent Marker",Impact,sans-serif;color:var(--white);font-size:15px;text-decoration:underline}
  .arrow{position:absolute;top:299px;width:28px;height:28px;border-radius:50%;background:#3a3a40;display:flex;align-items:center;justify-content:center}

  /* shows */
  .shows{top:1852px;height:491px;background:radial-gradient(ellipse at 50% 60%,#2a1f1c 0%,#141416 60%,#0d0d10 100%)}
  .shows h2{left:0;width:1200px;top:65px;text-align:center;font-size:32px}
  .show{position:absolute;top:140px;width:326px;height:264px;border-radius:18px;overflow:hidden}
  .show .art{position:absolute;inset:0}
  .show .a1{background:linear-gradient(160deg,#4a5a70 0%,#2a2f3a 50%,#6a4a30 100%)}
  .show .a2{background:linear-gradient(160deg,#5a5f6a 0%,#2f2a30 50%,#6a4a3a 100%)}
  .show .a3{background:linear-gradient(160deg,#3a3a44 0%,#6a4a30 50%,#a06a3a 100%)}
  .show .shade{position:absolute;inset:0;background:linear-gradient(180deg,rgba(0,0,0,0) 45%,rgba(0,0,0,.55) 100%)}
  .show h3{position:absolute;left:30px;top:172px;font-size:17px}
  .show .year{position:absolute;left:30px;top:196px;color:var(--white);font-size:18px}
  .show .rating{position:absolute;left:30px;top:228px;color:var(--white);font-size:12px}
  .show .btn{left:166px;top:186px;width:120px;height:42px;font-size:16px}

  /* services */
  .services{top:2343px;height:573px;background:linear-gradient(180deg,#151518 0%,#1a1a1e 60%,#121214 100%)}
  .services h2{left:96px;top:64px;font-size:32px}
  .service-list{position:absolute;left:96px;top:121px;list-style:none}
  .service-list li{display:flex;align-items:center;gap:9px;height:42.8px;font-size:15.5px;color:var(--white);white-space:nowrap}
  .frame{left:606px;top:80px;width:488px;height:419px;border:2px solid var(--red);border-top:none;border-right:none}
  .frame-top{left:606px;top:80px;width:14px;height:2px;background:var(--red)}
  .frame-right{left:1092px;top:480px;width:2px;height:19px;background:var(--red)}
  .studio{left:619px;top:71px;width:484px;height:414px;background:linear-gradient(150deg,#3e4a52 0%,#2a3036 45%,#6a6e72 100%)}

  /* footer */
  .footer{top:2916px;height:388px;background:var(--bg)}
  .footer .brand{left:0;width:1200px;justify-content:center;top:80px;font-size:72px}
  .footer .brand .mark{width:30px;height:30px}
  .footer-nav{position:absolute;top:216px;left:0;width:1200px;display:flex;justify-content:center;gap:47px;font-size:16px}
  .footer-nav a{color:var(--white);text-decoration:none}
  .copyright{left:0;width:1200px;top:278px;text-align:center;color:var(--white);font-size:16px}
</style>
</head>
<body>

<header class="section hero">
  <div class="brand abs"><span class="mark"></span>VORTIQ</div>
  <nav class="nav">
    <a class="active" href="#">Home</a>
    <a href="#">Account Information</a>
    <a href="#">Product</a>
  </nav>
  <a class="btn contact" href="#">Contact Us</a>
  <div class="devices abs" role="img" aria-label="Movie scene shown on a desktop, laptop, tablet and phone"></div>
  <h1 class="display abs">WELCOME TO<br>VORTIQ</h1>
  <p class="abs">Lorem ipsum dolor sit amet, consectetur adipiscing elit, sed do eiusmod tempor incididunt ut labore et dolore magna aliqua.</p>
  <a class="btn signup" href="#">Sign Up</a>
</header>

<section class="section about">
  <div class="phones abs" role="img" aria-label="Two smartphones showing the streaming app with a viewer watching a glowing screen"></div>
  <h2 class="display abs">ABOUT <span class="accent">US</span></h2>
  <p class="abs">Sed ut perspiciatis unde omnis iste natus error sit voluptatem accusantium doloremque laudantium, totam rem aperiam, eaque ipsa quae ab illo inventore veritatis et quasi architecto beatae vitae dicta sunt explicabo. Nemo enim ipsam voluptatem quia voluptas sit aspernatur aut odit aut fugit, sed quia consequuntur magni dolores eos qui ratione voluptatem sequi nesciunt. Neque porro quisquam est, qui dolorem ipsum quaerat voluptatem. Ut enim ad minima veniam, quis nostrum exercitationem ullam corporis suscipit molestiae consequatur, vel illum qui dolorem eum fugiat quo voluptas nulla pariatur?</p>
  <a class="btn more" href="#">READ MORE</a>
</section>

<section class="section benefits">
  <h2 class="display abs">BENEFITS AND <span class="accent">FEATURES</span></h2>
  <p class="lead abs">Lorem ipsum dolor sit amet, consectetur adipiscing elit, sed do eiusmod tempor incididunt ut labore et dolore magna aliqua.<br>Ut enim ad minim veniam, quis nostrud exercitation ullamco laboris nisi ut aliquip ex ea commodo consequat.</p>

  <div class="arrow" style="left:44px"><svg width="10" height="10" viewBox="0 0 10 10"><path d="M6.5 1.5 3 5l3.5 3.5" fill="none" stroke="#888" stroke-width="1.6"/></svg></div>
  <div class="arrow" style="left:1128px"><svg width="10" height="10" viewBox="0 0 10 10"><path d="M3.5 1.5 7 5 3.5 8.5" fill="none" stroke="#ddd" stroke-width="1.6"/></svg></div>

  <div class="card" style="left:113px">
    <div class="icon"><svg width="64" height="56" viewBox="0 0 64 56"><rect x="3" y="3" width="52" height="34" rx="3" fill="none" stroke="#e01010" stroke-width="3"/><path d="M22 44h16M29 37v7" stroke="#e01010" stroke-width="3"/><rect x="40" y="26" width="14" height="24" rx="3" transform="rotate(-30 47 38)" fill="#fff" stroke="#333" stroke-width="2.5"/><path d="M14 22a10 10 0 0 1 10-10M14 28a16 16 0 0 1 16-16" fill="none" stroke="#e01010" stroke-width="2.5"/></svg></div>
    <h3 class="display">LOREM IPSUM</h3>
    <p>Lorem ipsum dolor sit amet, consectetur adipiscing elit, sed do incididunt ut labore et dolore magna aliqua.</p>
    <a href="#">READ MORE</a>
  </div>
  <div class="card" style="left:444px">
    <div class="icon on"><svg width="64" height="56" viewBox="0 0 64 56"><rect x="3" y="3" width="52" height="34" rx="3" fill="none" stroke="#fff" stroke-width="3"/><path d="M22 44h16M29 37v7" stroke="#fff" stroke-width="3"/><rect x="40" y="26" width="14" height="24" rx="3" transform="rotate(-30 47 38)" fill="#e01010" stroke="#fff" stroke-width="2.5"/><path d="M14 22a10 10 0 0 1 10-10M14 28a16 16 0 0 1 16-16" fill="none" stroke="#fff" stroke-width="2.5"/></svg></div>
    <h3 class="display">LOREM IPSUM</h3>
    <p>Lorem ipsum dolor sit amet, consectetur adipiscing elit, sed do incididunt ut labore et dolore magna aliqua.</p>
    <a href="#">READ MORE</a>
  </div>
  <div class="card" style="left:774px">
    <div class="icon"><svg width="64" height="56" viewBox="0 0 64 56"><rect x="3" y="3" width="52" height="34" rx="3" fill="none" stroke="#e01010" stroke-width="3"/><path d="M22 44h16M29 37v7" stroke="#e01010" stroke-width="3"/><rect x="40" y="26" width="14" height="24" rx="3" transform="rotate(-30 47 38)" fill="#fff" stroke="#333" stroke-width="2.5"/><path d="M14 22a10 10 0 0 1 10-10M14 28a16 16 0 0 1 16-16" fill="none" stroke="#e01010" stroke-width="2.5"/></svg></div>
    <h3 class="display">LOREM IPSUM</h3>
    <p>Lorem ipsum dolor sit amet, consectetur adipiscing elit, sed do incididunt ut labore et dolore magna aliqua.</p>
    <a href="#">READ MORE</a>
  </div>
</section>

<section class="section shows">
  <h2 class="display abs">OUR POPULAR <span class="accent">TV SHOWS</span></h2>
  <article class="show" style="left:100px">
    <div class="art a1" role="img" aria-label="Viewer with popcorn watching a television"></div><div class="shade"></div>
    <h3 class="display">LOREM IPSUM</h3><span class="year">2022</span><span class="rating">7.8 Rating</span>
    <a class="btn" href="#">Watch Now</a>
  </article>
  <article class="show" style="left:438px">
    <div class="art a2" role="img" aria-label="Streaming menu on a television in a living room"></div><div class="shade"></div>
    <h3 class="display">LOREM IPSUM</h3><span class="year">2022</span><span class="rating">7.8 Rating</span>
    <a class="btn" href="#">Watch Now</a>
  </article>
  <article class="show" style="left:777px">
    <div class="art a3" role="img" aria-label="Family watching a show together"></div><div class="shade"></div>
    <h3 class="display">LOREM IPSUM</h3><span class="year">2022</span><span class="rating">7.8 Rating</span>
    <a class="btn" href="#">Watch Now</a>
  </article>
</section>

<section class="section services">
  <h2 class="display abs">OUR SERVICE <span class="accent">PROVIDE</span></h2>
  <ul class="service-list">
    <li><svg width="14" height="14" viewBox="0 0 14 14"><circle cx="7" cy="7" r="7" fill="#ff0f0f"/><path d="M3.8 7.2 6 9.3l4.2-4.4" fill="none" stroke="#fff" stroke-width="1.8"/></svg>Lorem ipsum dolor sit amet</li>
    <li><svg width="14" height="14" viewBox="0 0 14 14"><circle cx="7" cy="7" r="7" fill="#ff0f0f"/><path d="M3.8 7.2 6 9.3l4.2-4.4" fill="none" stroke="#fff" stroke-width="1.8"/></svg>Sed ut perspiciatis unde omnis</li>
    <li><svg width="14" height="14" viewBox="0 0 14 14"><circle cx="7" cy="7" r="7" fill="#ff0f0f"/><path d="M3.8 7.2 6 9.3l4.2-4.4" fill="none" stroke="#fff" stroke-width="1.8"/></svg>Voluptatem accusantium doloremque</li>
    <li><svg width="14" height="14" viewBox="0 0 14 14"><circle cx="7" cy="7" r="7" fill="#ff0f0f"/><path d="M3.8 7.2 6 9.3l4.2-4.4" fill="none" stroke="#fff" stroke-width="1.8"/></svg>At vero eos et accusamus et iusto odio</li>
    <li><svg width="14" height="14" viewBox="0 0 14 14"><circle cx="7" cy="7" r="7" fill="#ff0f0f"/><path d="M3.8 7.2 6 9.3l4.2-4.4" fill="none" stroke="#fff" stroke-width="1.8"/></svg>On the other hand, we denounce</li>
    <li><svg width="14" height="14" viewBox="0 0 14 14"><circle cx="7" cy="7" r="7" fill="#ff0f0f"/><path d="M3.8 7.2 6 9.3l4.2-4.4" fill="none" stroke="#fff" stroke-width="1.8"/></svg>Lorem ipsum dolor sit amet On the other hand, we denounce</li>
    <li><svg width="14" height="14" viewBox="0 0 14 14"><circle cx="7" cy="7" r="7" fill="#ff0f0f"/><path d="M3.8 7.2 6 9.3l4.2-4.4" fill="none" stroke="#fff" stroke-width="1.8"/></svg>Sed ut perspiciatis unde omnis denounce</li>
    <li><svg width="14" height="14" viewBox="0 0 14 14"><circle cx="7" cy="7" r="7" fill="#ff0f0f"/><path d="M3.8 7.2 6 9.3l4.2-4.4" fill="none" stroke="#fff" stroke-width="1.8"/></svg>Voluptatem accusantium doloremque we denounce</li>
    <li><svg width="14" height="14" viewBox="0 0 14 14"><circle cx="7" cy="7" r="7" fill="#ff0f0f"/><path d="M3.8 7.2 6 9.3l4.2-4.4" fill="none" stroke="#fff" stroke-width="1.8"/></svg>At vero eos et accusamus et iusto odio</li>
  </ul>
  <div class="frame abs"></div>
  <div class="frame-top abs"></div>
  <div class="studio abs" role="img" aria-label="Broadcast operator working at a control room mixing desk with monitors"></div>
  <div class="frame-right abs"></div>
</section>

<footer class="section footer">
  <div class="brand abs"><span class="mark"></span>VORTIQ</div>
  <nav class="footer-nav">
    <a href="#">Home</a>
    <a href="#">Account Information</a>
    <a href="#">Products</a>
  </nav>
  <p class="copyright abs">Copyrights@2023.VORTIQ.All Rights Reserved</p>
</footer>

</body>
</html>
```